Equipment Finance Specialist I work with companies who need the funds to buy their equipment

I would like a business card that stands out on the shelves. I want to be able to hand it to someone and say WOW. This card should have my logo.
You can put color into it I am very open on design and color

What my company does is we deal with dealerships that sell equipment such as Dump Trucks garbage trucks tractors trailers. Customers get referred to us and depending on their time in business we will ask for the following items

Companies that have been in business for more than two years we have a credit application program up to 250K . With this program we need the following items Credit application filled out(which is what I would like to be able for the customer to click on my website to get.) as well as three current month bank statements.

Deals over 250k we will need the following items

2 years business tax returns
2 years personal tax returns
Profit & Loss statement
Personal Financial Statement

what we do
100% FINANCING
SEASONAL PAYMENTS
LOAN BALLOON PAYMENTS
TRAC LEASING
LOW-INTEREST REFINANCING RATES
DEBT CONSOLIDATION

We specialize in creative financing solutions and offer a variety of reliable, flexible and expandable lending choices.

Target Market(s)

Trucking Companies

Industry/Entity Type

Trucking Company

Contact Information for Business Card

* $250,000 Application only Program
* Loans from $30,000 to 5,000,000
* Competitive Interest Rates

Font styles to use
Serif
Sans Serif

Colors

Designer to choose colors to be used in the design.

Requirements
Must have
• On the back of the card.
• * $250,000 Application only Program
• * Loans from $30,000 to 5,000,000
• My name, email, website. address
• * Competitive Interest Rates
• * 100% Financing
Nice to have
• I want my logo to pop on the card
• My logo is the great one I would like to use
Should not have
• I am up for your creativity as well

```html
<!DOCTYPE html>
<html lang="en">
<head>
<meta charset="utf-8">
<title>Summit Capital – Business Card</title>
<link href="https://fonts.googleapis.com/css2?family=Montserrat:wght@500;600;800&display=swap" rel="stylesheet">
<style>
  :root {
    --navy: #1b2a63;
    --navy-deep: #152254;
    --red: #e01f2d;
    --white: #ffffff;
    --paper: #f4f4f6;
    --backdrop: #e7e8ec;
    --ink: #1b2a63;
    --soft-white: rgba(255, 255, 255, .88);
  }
  * { box-sizing: border-box; margin: 0; padding: 0; }
  html, body {
    width: 1200px; height: 900px; overflow: hidden;
    background: var(--backdrop);
    font-family: "Montserrat", Arial, sans-serif;
  }
  .sheet {
    position: relative; width: 1200px; height: 900px;
    display: flex; flex-direction: column; align-items: center;
    justify-content: center; gap: 40px;
  }
  .card {
    position: relative; width: 665px; height: 380px;
    border-radius: 18px; overflow: hidden;
    box-shadow: 0 10px 30px rgba(20, 30, 70, .18);
  }

  /* Front */
  .card-front {
    background: linear-gradient(160deg, var(--white) 0%, var(--paper) 100%);
  }
  .brand {
    position: absolute; left: 48px; top: 42px;
    display: flex; align-items: center; gap: 12px;
  }
  .brand-dot {
    width: 40px; height: 40px; border-radius: 50%;
    background: var(--navy); flex: none;
  }
  .brand-name {
    font-weight: 800; font-size: 28px; letter-spacing: 1px;
    text-transform: uppercase; color: var(--navy); white-space: nowrap;
  }
  .divider {
    position: absolute; left: 48px; right: 118px; top: 196px;
    height: 2px; background: var(--red);
  }
  .contacts {
    position: absolute; left: 48px; top: 212px;
    list-style: none; font-size: 15px; font-weight: 500;
    color: var(--ink); line-height: 26px;
  }
  .contacts li { display: flex; align-items: center; gap: 10px; }
  .contacts svg { width: 13px; height: 13px; fill: var(--red); flex: none; }
  .contacts .accent { color: var(--red); }
  .person {
    position: absolute; right: 118px; top: 132px; text-align: right;
  }
  .person-name {
    font-weight: 600; font-size: 24px; color: var(--red);
    text-transform: uppercase; letter-spacing: .5px;
  }
  .person-title {
    font-weight: 500; font-size: 15px; color: var(--ink); margin-top: 4px;
  }
  .address {
    position: absolute; right: 118px; top: 212px; text-align: right;
    font-size: 15px; font-weight: 500; color: var(--ink); line-height: 24px;
  }
  .front-base { position: absolute; left: 0; bottom: 0; width: 665px; height: 60px; }

  /* Back */
  .card-back {
    background: linear-gradient(150deg, var(--navy) 0%, var(--navy-deep) 100%);
    padding: 46px 56px;
    display: flex; flex-direction: column; justify-content: center; gap: 30px;
  }
  .card-back .brand { position: static; gap: 18px; }
  .card-back .brand-dot { width: 64px; height: 64px; background: var(--white); }
  .card-back .brand-name { color: var(--white); font-size: 40px; letter-spacing: 2px; }
  .back-rule { width: 100%; height: 2px; background: var(--red); }
  .offers {
    list-style: none; display: grid; grid-template-columns: 1fr 1fr;
    gap: 14px 28px; color: var(--soft-white);
    font-size: 15px; font-weight: 600; line-height: 20px;
  }
  .offers li { display: flex; align-items: flex-start; gap: 10px; }
  .offers svg { width: 16px; height: 16px; flex: none; margin-top: 2px; }
</style>
</head>
<body>
<main class="sheet">

  <section class="card card-front" aria-label="Business card front">
    <div class="brand">
      <span class="brand-dot"></span>
      <span class="brand-name">Summit Capital</span>
    </div>

    <div class="person">
      <p class="person-name">Daniel Reyes</p>
      <p class="person-title">Director</p>
    </div>

    <div class="divider"></div>

    <ul class="contacts">
      <li>
        <svg viewBox="0 0 24 24" aria-hidden="true"><path d="M6.6 10.8a15.1 15.1 0 0 0 6.6 6.6l2.2-2.2a1 1 0 0 1 1-.25 11.4 11.4 0 0 0 3.6.57 1 1 0 0 1 1 1V20a1 1 0 0 1-1 1A17 17 0 0 1 3 4a1 1 0 0 1 1-1h3.5a1 1 0 0 1 1 1c0 1.25.2 2.450.57 3.57a1 1 0 0 1-.25 1z"/></svg>
        1300 472 615
      </li>
      <li>
        <svg viewBox="0 0 24 24" aria-hidden="true"><path d="M2 5h20v14H2zm2 2v.5l8 5 8-5V7zm0 2.8V17h16V9.8l-8 5z"/></svg>
        info@summitcapital.com
      </li>
      <li>
        <svg viewBox="0 0 24 24" aria-hidden="true"><circle cx="12" cy="12" r="10"/></svg>
        <span>www.<span class="accent">summitcapital</span>.com</span>
      </li>
    </ul>

    <p class="address">2185 Ridgeview Dr.<br>Allen, TX 75013</p>

    <svg class="front-base" viewBox="0 0 665 60" preserveAspectRatio="none" aria-hidden="true">
      <polygon points="0,34 250,34 250,42 0,42" fill="#e01f2d"/>
      <polygon points="238,60 262,30 665,30 665,60" fill="#ffffff"/>
      <polygon points="250,60 276,30 310,24 665,44 665,60" fill="#1b2a63"/>
      <polygon points="0,42 250,42 238,60 0,60" fill="#ffffff"/>
    </svg>
  </section>

  <section class="card card-back" aria-label="Business card back">
    <div class="brand">
      <span class="brand-dot"></span>
      <span class="brand-name">Summit Capital</span>
    </div>
    <div class="back-rule"></div>
    <ul class="offers">
      <li>
        <svg viewBox="0 0 24 24" aria-hidden="true"><path d="M4 12.5l5 5L20 6.5" fill="none" stroke="#e01f2d" stroke-width="3"/></svg>
        $250,000 Application Only Program
      </li>
      <li>
        <svg viewBox="0 0 24 24" aria-hidden="true"><path d="M4 12.5l5 5L20 6.5" fill="none" stroke="#e01f2d" stroke-width="3"/></svg>
        Loans from $30,000 to $5,000,000
      </li>
      <li>
        <svg viewBox="0 0 24 24" aria-hidden="true"><path d="M4 12.5l5 5L20 6.5" fill="none" stroke="#e01f2d" stroke-width="3"/></svg>
        Competitive Interest Rates
      </li>
      <li>
        <svg viewBox="0 0 24 24" aria-hidden="true"><path d="M4 12.5l5 5L20 6.5" fill="none" stroke="#e01f2d" stroke-width="3"/></svg>
        100% Financing
      </li>
    </ul>
  </section>

</main>
</body>
</html>
```